Recipe Card Design

I have a small kitchen store in Livingston Montana, and I would like to have recipe cards (4x6 postcard) designed with my logo, lines for recipe writing, all in black and white. My website is here: www.brambleforkcookware.com

Store

```html
<!DOCTYPE html>
<html lang="en">
<head>
<meta charset="utf-8">
<title>Bramble Fork Cookware – Recipe Card</title>
<link href="https://fonts.googleapis.com/css2?family=Chewy&display=swap" rel="stylesheet">
<style>
  :root {
    --ink: #1a1a1a;
    --rule: #333333;
    --band: #e6e6e6;
    --frame: #dcdcdc;
    --paper: #ffffff;
    --ghost: #ececec;
  }
  html, body {
    margin: 0;
    padding: 0;
    width: 1200px;
    height: 930px;
    overflow: hidden;
    background: var(--paper);
  }
  .card {
    position: relative;
    width: 1200px;
    height: 930px;
    font-family: "Chewy", "Comic Sans MS", cursive;
    color: var(--ink);
  }
  .brand {
    position: absolute;
    left: 92px;
    top: 28px;
    width: 253px;
    height: 292px;
    box-sizing: border-box;
    border: 4px solid var(--frame);
    display: flex;
    align-items: center;
    justify-content: center;
    text-align: center;
  }
  .brand-name {
    margin: 0;
    font-size: 40px;
    font-weight: 400;
    line-height: 1.1;
    color: var(--ink);
  }
  .band {
    position: absolute;
    background: var(--band);
  }
  .band::before,
  .band::after {
    content: "";
    position: absolute;
    left: 0;
    right: 0;
    height: 8px;
    background-repeat: repeat-x;
    background-size: 14px 8px;
  }
  .band::before {
    top: 0;
    background-image: radial-gradient(circle at 50% 0, var(--paper) 4px, transparent 4.5px);
  }
  .band::after {
    bottom: 0;
    background-image: radial-gradient(circle at 50% 100%, var(--paper) 4px, transparent 4.5px);
  }
  .title-band {
    left: 425px;
    top: 45px;
    width: 675px;
    height: 145px;
  }
  .title-label {
    position: absolute;
    left: 0;
    right: 0;
    top: 4px;
    text-align: center;
    font-size: 34px;
    margin: 0;
  }
  .footer-band {
    left: 105px;
    top: 823px;
    width: 995px;
    height: 68px;
  }
  .footer-label {
    position: absolute;
    top: 12px;
    font-size: 34px;
    margin: 0;
  }
  .serves { left: 18px; }
  .from { left: 277px; }
  .heading {
    position: absolute;
    margin: 0;
    font-size: 40px;
    font-weight: 400;
  }
  .directions-heading { left: 425px; width: 675px; top: 203px; text-align: center; }
  .ingredients-heading { left: 118px; top: 348px; }
  .ghost-mark {
    position: absolute;
    left: 780px;
    top: 425px;
    width: 380px;
    height: 400px;
    background: radial-gradient(ellipse at 55% 45%, var(--ghost), rgba(236,236,236,0) 70%);
  }
  .rules {
    position: absolute;
    left: 0;
    top: 0;
  }
  .rules line {
    stroke: var(--rule);
    stroke-width: 3;
    stroke-dasharray: 24 3;
  }
</style>
</head>
<body>
<main class="card">
  <div class="brand">
    <p class="brand-name">Bramble Fork<br>Cookware</p>
  </div>

  <section class="band title-band">
    <h1 class="title-label" style="font-weight:400">Recipe For:</h1>
  </section>

  <h2 class="heading directions-heading">Directions</h2>
  <h2 class="heading ingredients-heading">Ingredients</h2>

  <div class="ghost-mark" role="img" aria-label="Faint brand decoration"></div>

  <svg class="rules" width="1200" height="930" aria-hidden="true">
    <g class="direction-lines">
      <line x1="423" y1="270" x2="1100" y2="270"/>
      <line x1="423" y1="315" x2="1100" y2="315"/>
      <line x1="423" y1="360" x2="1100" y2="360"/>
      <line x1="423" y1="405" x2="1100" y2="405"/>
      <line x1="423" y1="450" x2="1100" y2="450"/>
      <line x1="423" y1="495" x2="1100" y2="495"/>
      <line x1="423" y1="540" x2="1100" y2="540"/>
      <line x1="423" y1="585" x2="1100" y2="585"/>
      <line x1="423" y1="630" x2="1100" y2="630"/>
      <line x1="423" y1="675" x2="1100" y2="675"/>
      <line x1="423" y1="718" x2="1100" y2="718"/>
      <line x1="423" y1="762" x2="1100" y2="762"/>
      <line x1="423" y1="806" x2="1100" y2="806"/>
    </g>
    <g class="ingredient-lines">
      <line x1="110" y1="428" x2="325" y2="428"/>
      <line x1="110" y1="468" x2="325" y2="468"/>
      <line x1="110" y1="508" x2="325" y2="508"/>
      <line x1="110" y1="548" x2="325" y2="548"/>
      <line x1="110" y1="588" x2="325" y2="588"/>
      <line x1="110" y1="628" x2="325" y2="628"/>
      <line x1="110" y1="668" x2="325" y2="668"/>
      <line x1="110" y1="708" x2="325" y2="708"/>
      <line x1="110" y1="748" x2="325" y2="748"/>
      <line x1="110" y1="790" x2="325" y2="790"/>
    </g>
  </svg>

  <footer class="band footer-band">
    <p class="footer-label serves">Serves</p>
    <p class="footer-label from">From the Kitchen of</p>
    <svg class="rules" width="995" height="68" aria-hidden="true">
      <line x1="135" y1="50" x2="235" y2="50"/>
      <line x1="590" y1="50" x2="970" y2="50"/>
    </svg>
  </footer>
</main>
</body>
</html>
```